Modern, clean business card for Clearbrook Optics

Updated business card with a modern look.

Logo on the front
Dr Tavin R Marquell and Associates on the front.
Three locations on the back:
Ridgefront Brantmart
509-555-0142
18342 E Fernhollow Ave

Pelham Brantmart
509-555-0187
4716 W Dunmore Ave

Copper Bluff Brantmart
509-555-0163
3854 S Kettering Rd

Facebook icon. www.clearbrookoptix.example

Nice open white space on back for writing next appointment time.

Target Market(s)

Main target is female 25-50, but I would like broad appeal.

Industry/Entity Type

Healthcare

Contact Information for Business Card

Modern look

Font styles to use
Serif

Requirements
Must have
• Logo and Dr Tavin R Marquell and Associates on front.
• 3 locations on back
• white space for noting next appointment

```html
<!DOCTYPE html>
<html lang="en">
<head>
<meta charset="utf-8">
<title>Clearbrook Optics – Business Card</title>
<link rel="stylesheet" href="https://fonts.googleapis.com/css2?family=Open+Sans:wght@400;600;700&display=swap">
<style>
  :root {
    --page: #e9e6e1;
    --blue-light: #1f86cf;
    --blue-dark: #0b5ea8;
    --navy: #1d2a5c;
    --paper: #f0f0f0;
    --paper-shade: #e3e4e6;
    --white: #ffffff;
  }
  * { box-sizing: border-box; margin: 0; padding: 0; }
  html, body { width: 1200px; height: 900px; overflow: hidden; }
  body {
    background: var(--page);
    font-family: "Open Sans", Arial, sans-serif;
    position: relative;
  }
  .card {
    position: absolute;
    left: 250px;
    width: 700px;
    height: 400px;
    overflow: hidden;
    box-shadow: 0 6px 18px rgba(0,0,0,0.18);
  }
  .card--back { top: 35px; background: var(--paper-shade); }
  .card--front { top: 465px; background: var(--paper); }

  /* Back */
  .back-band {
    position: absolute; left: 0; top: 0; width: 100%; height: 265px;
    background: linear-gradient(180deg, var(--blue-light), var(--blue-dark));
  }
  .location {
    position: absolute; color: var(--white);
  }
  .location__name { font-size: 20px; font-weight: 600; line-height: 1.15; margin-bottom: 12px; }
  .location__detail { font-size: 15px; line-height: 1.35; }
  .location--ridgefront { left: 50px; top: 120px; width: 190px; }
  .location--copper { left: 270px; top: 78px; width: 190px; }
  .location--pelham { left: 490px; top: 58px; width: 190px; }
  .divider {
    position: absolute; width: 1px; background: rgba(255,255,255,0.6);
  }
  .divider--one { left: 255px; top: 82px; height: 105px; }
  .divider--two { left: 475px; top: 60px; height: 90px; }
  .web {
    position: absolute; left: 0; width: 100%; top: 212px;
    display: flex; justify-content: center; align-items: center; gap: 16px;
    color: var(--white); font-size: 15px;
  }
  .web__social {
    width: 28px; height: 28px; border-radius: 5px; background: var(--white);
  }

  /* Front */
  .wave { position: absolute; left: 0; top: 0; }
  .brand {
    position: absolute; left: 95px; top: 130px;
    display: flex; align-items: center; gap: 16px;
  }
  .brand__dot {
    width: 34px; height: 34px; border-radius: 50%; background: var(--blue-light);
  }
  .brand__name {
    font-size: 46px; font-weight: 700; color: var(--navy); letter-spacing: 0.5px;
  }
  .practitioner {
    position: absolute; right: 32px; top: 262px;
    color: var(--white); font-size: 25px; font-weight: 600;
    transform: rotate(-9deg); transform-origin: right center;
  }
</style>
</head>
<body>

<section class="card card--back" aria-label="Card back with locations">
  <div class="back-band"></div>

  <div class="location location--ridgefront">
    <p class="location__name">Ridgefront Brantmart</p>
    <p class="location__detail">P: 509-555-0142<br>18342 E Fernhollow Ave</p>
  </div>
  <span class="divider divider--one"></span>
  <div class="location location--copper">
    <p class="location__name">Copper Bluff Brantmart</p>
    <p class="location__detail">P: 509-555-0163<br>3854 S Kettering Rd</p>
  </div>
  <span class="divider divider--two"></span>
  <div class="location location--pelham">
    <p class="location__name">Pelham Brantmart</p>
    <p class="location__detail">P: 509-555-0187<br>4716 W Dunmore Ave</p>
  </div>

  <div class="web">
    <span class="web__social" aria-hidden="true"></span>
    <span class="web__url">www.clearbrookoptix.example</span>
  </div>
</section>

<section class="card card--front" aria-label="Card front">
  <svg class="wave" width="700" height="400" viewBox="0 0 700 400" aria-hidden="true">
    <defs>
      <linearGradient id="waveBlue" x1="0" y1="0" x2="0" y2="1">
        <stop offset="0" stop-color="#1f86cf"/>
        <stop offset="1" stop-color="#0b5ea8"/>
      </linearGradient>
    </defs>
    <path d="M0,312 C190,312 390,262 560,180 C420,262 220,330 0,336 Z" fill="#1d2a5c"/>
    <path d="M0,344 C220,344 470,268 700,140 L700,400 L0,400 Z" fill="url(#waveBlue)"/>
  </svg>

  <div class="brand">
    <span class="brand__dot" aria-hidden="true"></span>
    <span class="brand__name">Clearbrook Optics</span>
  </div>

  <p class="practitioner">Dr Tavin R Marquell and Associates</p>
</section>

</body>
</html>
```